Camp Thornbrook 2021 Magazine Design

We are for someone to design our annual magazine/newsletter. This is a print newsletter that is a total of 20 pages. It will need to be designed in a way that is easy to share with our printers. The designer will need to be someone who is creative and easy to work with.
For those interested in this project we ask that you design 4 to 6 pages for us to view. Once we select the designer we will want the rest created in a two-week time span. For those submitting a bid please include front cover, theme & dates, mission & vision, and Make the Difference.

This link will provide the layout of the newsletter https://files.parcelvault.example/doc/7qzRk2LmVt9XwPa4NbHc6DsYe3FuJg8KoTiW5rQx/edit?share=1.

This link will provide you with the pictures that are needed and a few documents https://files.parcelvault.example/folders/4TpWx8QnRb2ZyLc7MfVd5HsJ?share=1

Details:
20 pages long (including covers)
8.5 x 11

Please message me if you need any further details.

Target Market(s)

Our alumni base. Covers all ages

Requirements
Must have
• Spelled out in document
Nice to have
• Spelled out in document
Should not have
• Spelled out in document

```html
<!DOCTYPE html>
<html lang="en">
<head>
<meta charset="utf-8">
<title>Camp Thornbrook 2021 – Table of Contents</title>
<link rel="stylesheet" href="https://fonts.googleapis.com/css2?family=Bebas+Neue&family=Oswald:wght@300&display=swap">
<style>
  :root {
    --strip-top: #d9d7cc;
    --strip-bottom: #c4c1ad;
    --panel-top: #ececea;
    --panel-bottom: #dedcd1;
    --header-band: #eeeeec;
    --cover-light: #f1f1f1;
    --cover-dark: #d6d6d6;
    --magazine: #3a2418;
    --title-red: #c8202f;
    --ink: #1f1f1f;
    --rule: #9a988e;
    --olive-top: #7b8469;
    --olive-mid: #58623f;
    --forest: #4a6232;
    --forest-light: #67833f;
    --meadow: #92a35e;
    --soil: #8c7c5a;
    --fade: #a9a68c;
  }
  * { box-sizing: border-box; margin: 0; padding: 0; }
  html, body { width: 927px; height: 1200px; overflow: hidden; }
  body { position: relative; background: var(--panel-bottom); font-family: "Oswald", "Arial Narrow", sans-serif; }

  .side-strip {
    position: absolute; left: 0; top: 0; width: 55px; height: 1200px;
    background: linear-gradient(90deg, var(--strip-bottom), var(--strip-top) 60%, #cfccbd);
  }
  .content-panel {
    position: absolute; left: 55px; top: 0; width: 342px; height: 1200px;
    background: linear-gradient(180deg, var(--panel-top), var(--panel-bottom));
  }
  .header-band {
    position: absolute; left: 55px; top: 0; width: 342px; height: 54px;
    background: linear-gradient(180deg, #e4e4e0, var(--header-band));
  }
  .issue-cover {
    position: absolute; left: 55px; top: 54px; width: 342px; height: 208px;
    overflow: hidden;
    background: radial-gradient(ellipse at 45% 45%, var(--cover-light), var(--cover-dark));
  }
  .issue-cover .cover-art {
    position: absolute; left: 78px; top: 27px; width: 195px; height: 161px;
  }

  .toc-title {
    position: absolute; left: 70px; top: 271px;
    font-family: "Bebas Neue", "Oswald", sans-serif;
    font-weight: 400; font-size: 29px; letter-spacing: 0.2px; color: var(--title-red);
  }

  .toc-list { position: absolute; left: 0; top: 310px; width: 397px; list-style: none; }
  .toc-item {
    position: relative; height: 41.8px; display: flex; align-items: flex-end;
    padding: 0 0 5px 70px; border-bottom: 1px dotted var(--rule);
    font-size: 16px; line-height: 20px; font-weight: 300; color: var(--ink);
  }
  .toc-item::after {
    content: ""; position: absolute; right: -3px; bottom: -3px;
    width: 6px; height: 6px; border-radius: 50%; background: #fff;
  }
  .toc-section { width: 219px; white-space: nowrap; }
  .toc-page { white-space: nowrap; }

  .feature-photo {
    position: absolute; left: 397px; top: 0; width: 530px; height: 1200px;
    background:
      linear-gradient(90deg, var(--fade) 0%, rgba(169,166,140,0.55) 12%, rgba(169,166,140,0) 22%),
      linear-gradient(180deg, var(--olive-top) 0%, var(--olive-mid) 30%, #4f5d39 38%, var(--forest) 50%, var(--forest-light) 68%, var(--meadow) 82%, var(--soil) 100%);
  }
</style>
</head>
<body>
  <div class="side-strip"></div>
  <div class="content-panel"></div>
  <div class="header-band"></div>

  <div class="issue-cover">
    <svg class="cover-art" role="img" aria-label="Mock-up of the 2021 magazine cover lying on a table" viewBox="0 0 195 161">
      <polygon points="0,40 110,0 195,110 80,161" fill="var(--magazine)"/>
    </svg>
  </div>

  <h1 class="toc-title">TABEL OF CONTENT</h1>

  <ol class="toc-list">
    <li class="toc-item"><span class="toc-section">Make the Difference</span><span class="toc-page">Page 3</span></li>
    <li class="toc-item"><span class="toc-section">Golf Tournament</span><span class="toc-page">Pages 5 &amp; 4</span></li>
    <li class="toc-item"><span class="toc-section">2021 Theme and Dates</span><span class="toc-page">Pages 7 &amp; 6</span></li>
    <li class="toc-item"><span class="toc-section">Where Are They Now: Dana Whitfield</span><span class="toc-page">Pages 9 &amp; 8</span></li>
    <li class="toc-item"><span class="toc-section">2019 Donors</span><span class="toc-page">Pages 12 &amp; ,11 ,10</span></li>
    <li class="toc-item"><span class="toc-section">2019 Thornbrook Awards</span><span class="toc-page">Page 13</span></li>
    <li class="toc-item"><span class="toc-section">Bee Rock</span><span class="toc-page">Pages 15&amp; 14</span></li>
    <li class="toc-item"><span class="toc-section">Mission/Vision</span><span class="toc-page">Pages 17 &amp; 16</span></li>
    <li class="toc-item"><span class="toc-section">A Place We Call Home</span><span class="toc-page">Page 18</span></li>
    <li class="toc-item"><span class="toc-section">Memorials</span><span class="toc-page">Page 19</span></li>
  </ol>

  <div class="feature-photo" role="img" aria-label="Photo of a carved tree stump cross in a forest clearing with stacked logs, fading into olive green at the top"></div>
</body>
</html>
```